Hello my Name is Elias Moreno. I buy and sell vintage comic books, you can refer to my instragram page qpkz.comics to get ideas and inspiration. For the front of the card I would like my company logo QPKZ Comics with a yellow and black background with the bat signal or bat emblem like on my IG page and with my info Elias Moreno as the Owner and address/ phone number, PO Box 617283, Palmvale, ZX 33827, 555-482-6170 and that I buy and sell comics & collectables . Also feel free to be open to other ideas if you want. Im not stuck on one design. For the back of the card I would like for it to say follow me on Instagram QPKZ.Comics with the ig emblem. Also would like the card to be vertical if possible. Thanks

```html
<!DOCTYPE html>
<html lang="en">
<head>
<meta charset="utf-8">
<title>QPKZ Comics – Business Card</title>
<link rel="stylesheet" href="https://fonts.googleapis.com/css2?family=Open+Sans:wght@400;600;700&display=swap">
<style>
  :root {
    --backdrop: #2a2a2b;
    --card: #141414;
    --brand-yellow: #f6c21c;
    --text-white: #f2f2f2;
    --divider: #262626;
  }
  * { box-sizing: border-box; margin: 0; padding: 0; }
  html, body {
    width: 1200px; height: 900px; overflow: hidden;
    background: var(--backdrop);
    font-family: "Open Sans", Arial, sans-serif;
  }
  .stage {
    position: relative; width: 1200px; height: 900px;
    display: flex; align-items: center; justify-content: center; gap: 50px;
  }
  .card {
    position: relative;
    width: 520px; height: 298px;
    background: var(--card);
    border-radius: 20px;
    box-shadow: 0 14px 30px rgba(0,0,0,.45);
    overflow: hidden;
  }
  .brand {
    position: absolute;
    display: flex; align-items: center; gap: 12px;
    color: var(--brand-yellow);
    font-weight: 700;
    font-size: 24px;
    letter-spacing: .5px;
    white-space: nowrap;
  }
  .brand-dot {
    width: 26px; height: 26px; border-radius: 50%;
    background: var(--brand-yellow);
    flex: none;
  }
  /* front */
  .card-front .brand { left: 40px; top: 132px; }
  .card-front .divider {
    position: absolute; left: 272px; top: 36px; bottom: 36px;
    width: 1px; background: var(--divider);
  }
  .contact {
    position: absolute; left: 300px; top: 76px;
    color: var(--text-white);
    white-space: nowrap;
  }
  .contact-name {
    color: var(--brand-yellow); font-weight: 700; font-size: 20px; line-height: 1.2;
  }
  .contact-role { font-size: 14px; margin: 2px 0 0 12px; }
  .contact-phone {
    display: flex; align-items: center; gap: 4px;
    font-size: 15px; margin: 18px 0 0 26px;
  }
  .contact-phone svg { width: 13px; height: 13px; fill: var(--brand-yellow); }
  .contact-address { font-size: 15px; line-height: 1.45; margin: 12px 0 0 42px; }
  /* back */
  .card-back .brand { left: 40px; top: 112px; }
  .follow {
    position: absolute; left: 290px; top: 78px;
    color: var(--brand-yellow);
    white-space: nowrap;
  }
  .follow-label { font-weight: 600; font-size: 15px; }
  .follow-handle {
    display: flex; align-items: center; gap: 8px;
    margin: 10px 0 0 16px; font-size: 13px; font-weight: 600;
  }
  .follow-mark { width: 20px; height: 20px; border-radius: 5px; background: var(--brand-yellow); }
  .tagline {
    position: absolute; left: 0; right: 0; bottom: 58px;
    text-align: center;
    color: var(--brand-yellow); font-weight: 700; font-size: 19px;
  }
</style>
</head>
<body>
<main class="stage">
  <section class="card card-front" aria-label="Card front">
    <div class="brand"><span class="brand-dot"></span>QPKZ Comics</div>
    <div class="divider"></div>
    <div class="contact">
      <p class="contact-name">Elias Moreno</p>
      <p class="contact-role">Owner</p>
      <p class="contact-phone">
        <svg viewBox="0 0 24 24" aria-hidden="true"><path d="M6.6 10.8a15.1 15.1 0 0 0 6.6 6.6l2.2-2.2a1 1 0 0 1 1-.25 11.4 11.4 0 0 0 3.6.57 1 1 0 0 1 1 1V20a1 1 0 0 1-1 1A17 17 0 0 1 3 4a1 1 0 0 1 1-1h3.5a1 1 0 0 1 1 1c0 1.25.2 2.45.57 3.6a1 1 0 0 1-.25 1z"/></svg>
        555-482-6170
      </p>
      <p class="contact-address">PO Box 617283<br>Palmvale, ZX 33827</p>
    </div>
  </section>

  <section class="card card-back" aria-label="Card back">
    <div class="brand"><span class="brand-dot"></span>QPKZ Comics</div>
    <div class="follow">
      <p class="follow-label">Follow me on</p>
      <p class="follow-handle"><span class="follow-mark"></span>QPKZ.Comics</p>
    </div>
    <p class="tagline">We buy and sell comics &amp; collectables</p>
  </section>
</main>
</body>
</html>
```